Church Website with Home Page and Member Sermon Library

I am in need of an updated design for our church website. This will include 4 pages (outlined below). We are a conservative, evangelical, Christian church. The site should be modern and clean, while still reflecting our conservative values. I already have a logo for our church, and I want the site to incorporate the logo, and match the logo/branding. Stock photos are allowed if needed, but I have uploaded some images of our church and would prefer those images to be used if possible. Any stock photos used should not include any people in the photos (scenery, nature, buildings, animals, etc. are fine).

The site will need 4 pages: Home, Support Us (Donate), Login, and Recording Library.

Page 1: Home
The home page should include the following sections:

- Navigation: Should include links to each section of the home page plus a "listen live" link which will take the user to a live-streaming site and a "support us" link which will take the user to a support/donate page.

- Announcements: Can be either a banner or some other design, but there needs to be some way for us to post announcements for visitors to see. I'm open for creative ideas in this section, but would like it not to take up a lot of room on the page.

- About Us: Should include address, service times (see attached document), and information about the church.

- Pastor Bio: A section that introduces our pastor and gives a short bio about our pastor. Would like this section to include a picture of our pastor. Somewhere in this section I would like to include this Bible reference: "And I will give you pastors according to mine heart, which shall feed you with knowledge and understanding. Jer 3:15 LPW"

- Articles of Faith (What We Believe): This should include several sub-sections each with a heading, body, and possibly 1 or more scripture references. I have attached a document to the brief that includes our articles of faith. Feel free to be creative with this section in how you lay these out and format them.

- Support Us: A small section that explains what kind of support someone can give and a link to a donation page. The link can say something like "Support Us" or "Donate Now".

- Contact form: A contact form that allows the visitor to send us a message. The contact form should ask for name, email, phone, and message.

- Footer: A footer that will be displayed on all pages of the site. This should include at a minimum a link to the home page (or a link to each individual section in the home page if you prefer), a link to "listen live", a link to "support us", a link to "contact us" (or you can put the contact form directly in the footer if you prefer), the address, and a "member login" link.

Page 2: Support Us
The donation page should include a form the visitor can fill out to make a donation. We will embed a third party form later. For this design, please just mock out the design with a basic form asking for name, phone, and email.

Page 3: Login
The recording library (detailed below) will require members to login with a shared numeric code before accessing the page. We need a design for a login screen. The screen should include navigation/footer just like all other pages, but the body of the login page will consist only of a form that asks the user to enter the access code and then a "login" button.

Page 4: Recording Library

The library page is a member-only page that will require a shared, numeric pass code to access. On this page, members will be able to access a filterable list of past sermons. The page by default should display most recent sermons, but should also include a search form that allows the member to filter the sermon list to find a particular sermon. The search form should allow the user to select a filter type (e.g. Speaker name, date, event, etc.) and type in a value to search. They should be able to add multiple filters and remove filters that have been added. Each sermon that is displayed in the result list should include basic information such as title, date, speaker, tags, etc. along with a download icon, and an embedded audio player where they can click a play button to stream it on-demand. Each sermon should also have clickable tags associated with it that can be used to find related sermons.
Updates

I have uploaded several images of our church. Feel free to incorporate these into your design if possible.

Target Market(s)

Church Members

Industry/Entity Type

Religion

Number of Pages Required

4 page

Font styles to use
Sans Serif

Colors

Designer to choose colors to be used in the design.

Requirements
Must have
• Must incorporate the logo (attached)
Nice to have
• Would like the design to incorporate pictures of our church (attached) instead of stock photos if possible.
Should not have
• Please avoid an overly cluttered design. Stock photos used should not include any people in the photos.

```html
<!DOCTYPE html>
<html lang="en">
<head>
<meta charset="utf-8">
<title>Grace Hill Chapel – Holy Sermons Library</title>
<link href="https://fonts.googleapis.com/css2?family=Outfit:wght@300;400;500;600;700;800&display=swap" rel="stylesheet">
<style>
:root{
  --ink:#1f1f1c;
  --paper:#ffffff;
  --header-bg:#f5f5f7;
  --field-bg:#f6f2f3;
  --field-line:#e4e1e2;
  --rule:#7f8a7a;
  --pic-label:#5c5c58;
  --accent:#1ebed6;
  --brand:#4a8a55;
  --grad-top:#e7eede;
  --grad-green:#9ccc72;
  --grad-mid:#6cc49a;
  --grad-bottom:#1cbdd6;
}
*{box-sizing:border-box;margin:0;padding:0}
html,body{width:944px;height:1200px;overflow:hidden}
body{font-family:'Outfit',sans-serif;color:var(--ink);background:var(--paper);position:relative}

/* Sidebar */
.sidebar{position:absolute;left:0;top:0;width:177px;height:827px;background:var(--paper)}
.brand{position:absolute;left:36px;top:30px;display:flex;align-items:center;gap:7px}
.brand-mark{width:18px;height:18px;border-radius:50%;background:var(--brand)}
.brand-name{font-size:13px;font-weight:500;color:var(--brand)}
.nav-item{position:absolute;left:28px;display:flex;align-items:center;gap:11px;font-size:12px;font-weight:600;color:var(--ink);text-decoration:none}
.nav-item svg{width:16px;height:16px}
.nav-item.underlined span{text-decoration:underline}
.playlist-heading{position:absolute;left:55px;top:233px;font-size:9.5px;font-weight:700}
.playlist-link{position:absolute;left:63px;font-size:9.5px;font-weight:400;color:var(--ink)}
.playlist-link.current{text-decoration:underline}

/* Header */
.topbar{position:absolute;left:177px;top:0;width:767px;height:78px;background:var(--header-bg)}
.search{position:absolute;left:40px;top:19px;display:flex;height:40px}
.search-input{width:214px;height:40px;background:var(--field-bg);border:1px solid var(--field-line);border-right:none;font-size:11px;color:#77777a;padding:0 12px;display:flex;align-items:center}
.search-category{width:123px;height:40px;background:var(--field-bg);border:1px solid var(--field-line);font-size:11.5px;font-weight:500;padding:0 11px;display:flex;align-items:center;justify-content:space-between}
.search-button{width:41px;height:40px;background:var(--ink);display:flex;align-items:center;justify-content:center}
.pager{position:absolute;right:28px;top:28px;display:flex;gap:7px}
.pager svg{width:22px;height:22px}

/* Library */
.library{position:absolute;left:177px;top:78px;width:767px;height:749px;
  background:linear-gradient(180deg,var(--grad-top) 0%,var(--grad-green) 32%,var(--grad-mid) 62%,var(--grad-bottom) 100%)}
.page-title{position:absolute;left:52px;top:34px}
.page-title h1{font-size:32px;font-weight:800;letter-spacing:-.3px;line-height:1}
.page-title p{font-size:16px;font-weight:400;margin-top:1px}
.shelf{position:absolute;left:19px;width:729px;border-top:1px solid var(--rule)}
.shelf h2{position:absolute;left:12px;top:13px;font-size:16px;font-weight:600}
.cards{position:absolute;left:8px;top:45px;display:flex;gap:23px}
.card{width:99px}
.card-pic{position:relative;width:99px;height:99px;background:var(--ink);border-radius:8px;display:flex;align-items:center;justify-content:center;font-size:17px;font-weight:600;color:var(--pic-label)}
.card-actions{position:absolute;right:7px;bottom:5px;display:flex;gap:5px}
.card-actions svg{width:9px;height:9px}
.card-title{font-size:11px;font-weight:700;margin:7px 0 0 8px}
.card-desc{font-size:7.4px;margin:3px 0 0 8px}
.card-meta{font-size:7px;margin:6px 0 0 8px}

/* Footer */
.footer{position:absolute;left:0;top:827px;width:944px;height:373px;background:var(--ink);color:#fff}
.col{position:absolute;top:58px}
.col h3{font-size:15px;font-weight:800;letter-spacing:.2px}
.col a{display:block;color:#fff;text-decoration:none;font-size:16px;font-weight:300;margin-top:19px;line-height:1.2}
.col-find p{font-size:16px;font-weight:300;line-height:1.18;margin-top:14px}
.col-find h3.write{margin-top:11px}
.col-find a.mail{text-decoration:underline;margin-top:14px}
.socials{display:flex;gap:12px;margin-top:22px}
.social{display:flex;align-items:center;gap:5px;font-size:10px;font-weight:500;color:#fff}
.social-dot{width:14px;height:14px;border-radius:50%;background:#fff}
.legal{position:absolute;left:236px;top:322px;font-size:15.5px;font-weight:300}
.legal a{color:var(--accent)}
</style>
</head>
<body>

<aside class="sidebar">
  <div class="brand"><span class="brand-mark"></span><span class="brand-name">Grace Hill Chapel</span></div>

  <a class="nav-item" style="top:100px" href="#">
    <svg viewBox="0 0 16 16"><path d="M8 1.5 1 7.5h2v7h4v-4h2v4h4v-7h2z" fill="#1f1f1c"/></svg><span>Home</span></a>
  <a class="nav-item" style="top:135px" href="#">
    <svg viewBox="0 0 16 16" fill="none" stroke="#1f1f1c" stroke-width="1.2"><rect x="1.5" y="2" width="3" height="12"/><rect x="5.5" y="3" width="3" height="11"/><path d="m9.5 3.5 2.8-.8 2.2 10.8-2.8.6z"/><path d="M1 14.5h14"/></svg><span>Library</span></a>
  <a class="nav-item" style="top:170px" href="#">
    <svg viewBox="0 0 16 16"><path d="M8 14.5S1 10.2 1 5.4A3.6 3.6 0 0 1 8 4a3.6 3.6 0 0 1 7 1.4c0 4.8-7 9.1-7 9.1z" fill="#1f1f1c"/></svg><span>Favorites</span></a>
  <a class="nav-item underlined" style="top:205px" href="#">
    <svg viewBox="0 0 16 16"><circle cx="8" cy="8" r="7" fill="#1f1f1c"/><path d="M8 4.5v7M4.5 8h7" stroke="#fff" stroke-width="1.4"/></svg><span>Create Playlist</span></a>

  <div class="playlist-heading">YOUR PLAYLIST</div>
  <a class="playlist-link current" style="top:253px">Holy Sermon 2023</a>
  <a class="playlist-link" style="top:273px">Existence</a>
  <a class="playlist-link" style="top:293px">Marriage</a>

  <a class="nav-item" style="top:398px" href="#">
    <svg viewBox="0 0 16 16" fill="none" stroke="#1f1f1c" stroke-width="1.3"><circle cx="8" cy="8" r="6.8"/><ellipse cx="8" cy="8" rx="3" ry="6.8"/><path d="M1.2 8h13.6M2.3 4.6h11.4M2.3 11.4h11.4"/></svg><span>English</span></a>
</aside>

<header class="topbar">
  <div class="search">
    <div class="search-input">Search</div>
    <div class="search-category"><span>Category</span>
      <svg width="7" height="5" viewBox="0 0 7 5"><path d="m1 1 2.5 2.5L6 1" stroke="#1f1f1c" fill="none" stroke-width="1.2"/></svg></div>
    <div class="search-button">
      <svg width="18" height="18" viewBox="0 0 18 18" fill="none" stroke="#fff" stroke-width="1.8"><circle cx="7.5" cy="7.5" r="5.8"/><path d="m11.8 11.8 4.8 4.8"/></svg></div>
  </div>
  <div class="pager">
    <svg viewBox="0 0 22 22" fill="none" stroke="#1f1f1c" stroke-width="1.5"><circle cx="11" cy="11" r="10"/><path d="m12.5 7-4 4 4 4"/></svg>
    <svg viewBox="0 0 22 22" fill="none" stroke="#1f1f1c" stroke-width="1.5"><circle cx="11" cy="11" r="10"/><path d="m9.5 7 4 4-4 4"/></svg>
  </div>
</header>

<main class="library" role="img" aria-label="Soft green-to-teal wash over a photo of the church building exterior">
  <div class="page-title"><h1>HOLY SERMONS</h1><p>2023</p></div>

  <section class="shelf" style="top:100px">
    <h2>Corinthians</h2>
    <div class="cards">
      <article class="card"><div class="card-pic" role="img" aria-label="Sermon cover artwork">PIC<div class="card-actions"><svg viewBox="0 0 10 10"><path d="M5 1v8M1 5h8" stroke="#fff" stroke-width="1.3"/></svg><svg viewBox="0 0 10 10"><path d="M5 9S.5 6.3.5 3.3A2.2 2.2 0 0 1 5 2.4a2.2 2.2 0 0 1 4.5.9C9.5 6.3 5 9 5 9z" fill="#fff"/></svg></div></div><div class="card-title">TITLE</div><div class="card-desc">A very short description.</div><div class="card-meta">32 mins · Febuary 12</div></article>
      <article class="card"><div class="card-pic" role="img" aria-label="Sermon cover artwork">PIC<div class="card-actions"><svg viewBox="0 0 10 10"><path d="M5 1v8M1 5h8" stroke="#fff" stroke-width="1.3"/></svg><svg viewBox="0 0 10 10"><path d="M5 9S.5 6.3.5 3.3A2.2 2.2 0 0 1 5 2.4a2.2 2.2 0 0 1 4.5.9C9.5 6.3 5 9 5 9z" fill="#fff"/></svg></div></div><div class="card-title">TITLE</div><div class="card-desc">A very short description.</div><div class="card-meta">32 mins · Febuary 12</div></article>
      <article class="card"><div class="card-pic" role="img" aria-label="Sermon cover artwork">PIC<div class="card-actions"><svg viewBox="0 0 10 10"><path d="M5 1v8M1 5h8" stroke="#fff" stroke-width="1.3"/></svg><svg viewBox="0 0 10 10"><path d="M5 9S.5 6.3.5 3.3A2.2 2.2 0 0 1 5 2.4a2.2 2.2 0 0 1 4.5.9C9.5 6.3 5 9 5 9z" fill="#fff"/></svg></div></div><div class="card-title">TITLE</div><div class="card-desc">A very short description.</div><div class="card-meta">32 mins · Febuary 12</div></article>
      <article class="card"><div class="card-pic" role="img" aria-label="Sermon cover artwork">PIC<div class="card-actions"><svg viewBox="0 0 10 10"><path d="M5 1v8M1 5h8" stroke="#fff" stroke-width="1.3"/></svg><svg viewBox="0 0 10 10"><path d="M5 9S.5 6.3.5 3.3A2.2 2.2 0 0 1 5 2.4a2.2 2.2 0 0 1 4.5.9C9.5 6.3 5 9 5 9z" fill="#fff"/></svg></div></div><div class="card-title">TITLE</div><div class="card-desc">A very short description.</div><div class="card-meta">32 mins · Febuary 12</div></article>
      <article class="card"><div class="card-pic" role="img" aria-label="Sermon cover artwork">PIC<div class="card-actions"><svg viewBox="0 0 10 10"><path d="M5 1v8M1 5h8" stroke="#fff" stroke-width="1.3"/></svg><svg viewBox="0 0 10 10"><path d="M5 9S.5 6.3.5 3.3A2.2 2.2 0 0 1 5 2.4a2.2 2.2 0 0 1 4.5.9C9.5 6.3 5 9 5 9z" fill="#fff"/></svg></div></div><div class="card-title">TITLE</div><div class="card-desc">A very short description.</div><div class="card-meta">32 mins · Febuary 12</div></article>
      <article class="card"><div class="card-pic" role="img" aria-label="Sermon cover artwork">PIC<div class="card-actions"><svg viewBox="0 0 10 10"><path d="M5 1v8M1 5h8" stroke="#fff" stroke-width="1.3"/></svg><svg viewBox="0 0 10 10"><path d="M5 9S.5 6.3.5 3.3A2.2 2.2 0 0 1 5 2.4a2.2 2.2 0 0 1 4.5.9C9.5 6.3 5 9 5 9z" fill="#fff"/></svg></div></div><div class="card-title">TITLE</div><div class="card-desc">A very short description.</div><div class="card-meta">32 mins · Febuary 12</div></article>
    </div>
  </section>

  <section class="shelf" style="top:316px">
    <h2>Matthew 12</h2>
    <div class="cards">
      <article class="card"><div class="card-pic" role="img" aria-label="Sermon cover artwork">PIC<div class="card-actions"><svg viewBox="0 0 10 10"><path d="M5 1v8M1 5h8" stroke="#fff" stroke-width="1.3"/></svg><svg viewBox="0 0 10 10"><path d="M5 9S.5 6.3.5 3.3A2.2 2.2 0 0 1 5 2.4a2.2 2.2 0 0 1 4.5.9C9.5 6.3 5 9 5 9z" fill="#fff"/></svg></div></div><div class="card-title">TITLE</div><div class="card-desc">A very short description.</div><div class="card-meta">32 mins · Febuary 12</div></article>
      <article class="card"><div class="card-pic" role="img" aria-label="Sermon cover artwork">PIC<div class="card-actions"><svg viewBox="0 0 10 10"><path d="M5 1v8M1 5h8" stroke="#fff" stroke-width="1.3"/></svg><svg viewBox="0 0 10 10"><path d="M5 9S.5 6.3.5 3.3A2.2 2.2 0 0 1 5 2.4a2.2 2.2 0 0 1 4.5.9C9.5 6.3 5 9 5 9z" fill="#fff"/></svg></div></div><div class="card-title">TITLE</div><div class="card-desc">A very short description.</div><div class="card-meta">32 mins · Febuary 12</div></article>
      <article class="card"><div class="card-pic" role="img" aria-label="Sermon cover artwork">PIC<div class="card-actions"><svg viewBox="0 0 10 10"><path d="M5 1v8M1 5h8" stroke="#fff" stroke-width="1.3"/></svg><svg viewBox="0 0 10 10"><path d="M5 9S.5 6.3.5 3.3A2.2 2.2 0 0 1 5 2.4a2.2 2.2 0 0 1 4.5.9C9.5 6.3 5 9 5 9z" fill="#fff"/></svg></div></div><div class="card-title">TITLE</div><div class="card-desc">A very short description.</div><div class="card-meta">32 mins · Febuary 12</div></article>
      <article class="card"><div class="card-pic" role="img" aria-label="Sermon cover artwork">PIC<div class="card-actions"><svg viewBox="0 0 10 10"><path d="M5 1v8M1 5h8" stroke="#fff" stroke-width="1.3"/></svg><svg viewBox="0 0 10 10"><path d="M5 9S.5 6.3.5 3.3A2.2 2.2 0 0 1 5 2.4a2.2 2.2 0 0 1 4.5.9C9.5 6.3 5 9 5 9z" fill="#fff"/></svg></div></div><div class="card-title">TITLE</div><div class="card-desc">A very short description.</div><div class="card-meta">32 mins · Febuary 12</div></article>
      <article class="card"><div class="card-pic" role="img" aria-label="Sermon cover artwork">PIC<div class="card-actions"><svg viewBox="0 0 10 10"><path d="M5 1v8M1 5h8" stroke="#fff" stroke-width="1.3"/></svg><svg viewBox="0 0 10 10"><path d="M5 9S.5 6.3.5 3.3A2.2 2.2 0 0 1 5 2.4a2.2 2.2 0 0 1 4.5.9C9.5 6.3 5 9 5 9z" fill="#fff"/></svg></div></div><div class="card-title">TITLE</div><div class="card-desc">A very short description.</div><div class="card-meta">32 mins · Febuary 12</div></article>
      <article class="card"><div class="card-pic" role="img" aria-label="Sermon cover artwork">PIC<div class="card-actions"><svg viewBox="0 0 10 10"><path d="M5 1v8M1 5h8" stroke="#fff" stroke-width="1.3"/></svg><svg viewBox="0 0 10 10"><path d="M5 9S.5 6.3.5 3.3A2.2 2.2 0 0 1 5 2.4a2.2 2.2 0 0 1 4.5.9C9.5 6.3 5 9 5 9z" fill="#fff"/></svg></div></div><div class="card-title">TITLE</div><div class="card-desc">A very short description.</div><div class="card-meta">32 mins · Febuary 12</div></article>
    </div>
  </section>

  <section class="shelf" style="top:532px">
    <h2>Funeral</h2>
    <div class="cards">
      <article class="card"><div class="card-pic" role="img" aria-label="Sermon cover artwork">PIC<div class="card-actions"><svg viewBox="0 0 10 10"><path d="M5 1v8M1 5h8" stroke="#fff" stroke-width="1.3"/></svg><svg viewBox="0 0 10 10"><path d="M5 9S.5 6.3.5 3.3A2.2 2.2 0 0 1 5 2.4a2.2 2.2 0 0 1 4.5.9C9.5 6.3 5 9 5 9z" fill="#fff"/></svg></div></div><div class="card-title">TITLE</div><div class="card-desc">A very short description.</div><div class="card-meta">32 mins · Febuary 12</div></article>
      <article class="card"><div class="card-pic" role="img" aria-label="Sermon cover artwork">PIC<div class="card-actions"><svg viewBox="0 0 10 10"><path d="M5 1v8M1 5h8" stroke="#fff" stroke-width="1.3"/></svg><svg viewBox="0 0 10 10"><path d="M5 9S.5 6.3.5 3.3A2.2 2.2 0 0 1 5 2.4a2.2 2.2 0 0 1 4.5.9C9.5 6.3 5 9 5 9z" fill="#fff"/></svg></div></div><div class="card-title">TITLE</div><div class="card-desc">A very short description.</div><div class="card-meta">32 mins · Febuary 12</div></article>
      <article class="card"><div class="card-pic" role="img" aria-label="Sermon cover artwork">PIC<div class="card-actions"><svg viewBox="0 0 10 10"><path d="M5 1v8M1 5h8" stroke="#fff" stroke-width="1.3"/></svg><svg viewBox="0 0 10 10"><path d="M5 9S.5 6.3.5 3.3A2.2 2.2 0 0 1 5 2.4a2.2 2.2 0 0 1 4.5.9C9.5 6.3 5 9 5 9z" fill="#fff"/></svg></div></div><div class="card-title">TITLE</div><div class="card-desc">A very short description.</div><div class="card-meta">32 mins · Febuary 12</div></article>
      <article class="card"><div class="card-pic" role="img" aria-label="Sermon cover artwork">PIC<div class="card-actions"><svg viewBox="0 0 10 10"><path d="M5 1v8M1 5h8" stroke="#fff" stroke-width="1.3"/></svg><svg viewBox="0 0 10 10"><path d="M5 9S.5 6.3.5 3.3A2.2 2.2 0 0 1 5 2.4a2.2 2.2 0 0 1 4.5.9C9.5 6.3 5 9 5 9z" fill="#fff"/></svg></div></div><div class="card-title">TITLE</div><div class="card-desc">A very short description.</div><div class="card-meta">32 mins · Febuary 12</div></article>
      <article class="card"><div class="card-pic" role="img" aria-label="Sermon cover artwork">PIC<div class="card-actions"><svg viewBox="0 0 10 10"><path d="M5 1v8M1 5h8" stroke="#fff" stroke-width="1.3"/></svg><svg viewBox="0 0 10 10"><path d="M5 9S.5 6.3.5 3.3A2.2 2.2 0 0 1 5 2.4a2.2 2.2 0 0 1 4.5.9C9.5 6.3 5 9 5 9z" fill="#fff"/></svg></div></div><div class="card-title">TITLE</div><div class="card-desc">A very short description.</div><div class="card-meta">32 mins · Febuary 12</div></article>
      <article class="card"><div class="card-pic" role="img" aria-label="Sermon cover artwork">PIC<div class="card-actions"><svg viewBox="0 0 10 10"><path d="M5 1v8M1 5h8" stroke="#fff" stroke-width="1.3"/></svg><svg viewBox="0 0 10 10"><path d="M5 9S.5 6.3.5 3.3A2.2 2.2 0 0 1 5 2.4a2.2 2.2 0 0 1 4.5.9C9.5 6.3 5 9 5 9z" fill="#fff"/></svg></div></div><div class="card-title">TITLE</div><div class="card-desc">A very short description.</div><div class="card-meta">32 mins · Febuary 12</div></article>
    </div>
  </section>
</main>

<footer class="footer">
  <div class="col" style="left:236px">
    <h3>WHO WE ARE</h3>
    <a href="#">About us</a><a href="#">Ministries</a><a href="#">Events</a>
  </div>
  <div class="col" style="left:387px">
    <h3>INFO</h3>
    <a href="#">Careers</a><a href="#">Community</a><a href="#">Blog</a><a href="#">Press</a>
  </div>
  <div class="col" style="left:499px">
    <h3>HELP</h3>
    <a href="#">Contact us</a><a href="#">FAQ</a><a href="#">Legal &amp; Privacy</a>
  </div>
  <div class="col col-find" style="left:638px">
    <h3>FIND US AT</h3>
    <p>(555) 014-0219<br>Alder Crest Rd, Maplewood,<br>Ohio(OH), 40000</p>
    <h3 class="write">WRITE TO US</h3>
    <a class="mail" href="#">hello@gracehillchapel.org</a>
    <div class="socials">
      <span class="social"><span class="social-dot"></span>Streamly</span>
      <span class="social"><span class="social-dot"></span>Friendly</span>
      <span class="social"><span class="social-dot"></span>Chirper</span>
      <span class="social"><span class="social-dot"></span>Wireline</span>
    </div>
  </div>
  <p class="legal">© 2021 Lumenfold. All Rights Reserved. <a href="#">Privacy Policy</a></p>
</footer>

</body>
</html>
```